WE ARE BRIGHT SPARROW, building a full website with ecommerce

requirements:
CODED FOR SITEQUILL
ONLINE STORE FUNCTION WITH E-COMMERCE USING TRADEBLOOM
PAGEWAVE AND PICTOLANE LINKS

I need a website design for my organization, WE ARE BRIGHT SPARROW, a global empowerment movement elevating woman, and the world. The site's home page should reflect our mission, to empower women. It should have a strong, empowering feel, with minimalistic design.
Please see www.lunavelto.com and http://www.corvenhal.co/ for an inspiration on layout and feel.

**PLEASE SEE ATTACHMENT "LOGO MOCK UP" FOR LOGO. THIS IS NOT THE FINAL VECTOR FILE, BUT THIS LOOKS THE SAME AS THE FINAL LOGO.

HOME PAGE:
The first section of the home page should include a background image with our logo center.

You should include the following links to pages at the top right of the page:
MISSION
MANTRA
ARMOR
MEET BS (I would like "bs" to be our logo)
pagewave and pictolane links

As you scroll down the page, you should see the following sections, which correlate to the links to pages as written above. **SEE ATTACHED SKETCH "HOMEPAGE LAYOUT IDEA" FOR REFERENCE**

WHO WE ARE (correlates to the link Mission)

OUR MANTRA (correlates to the link Mantra)

OUR ARMOR (correlates to the link The Shirt)
(This is where we will sell a shirt (and other apparel) and need the e-commerce function)

MEET BRIGHT SPARROWS (correlates to the link Meet BS)

SHOW OFF YOUR SUPER POWERS (correlates to the pagewave and pictolane)

FEATURED BRIGHT SPARROW (no link on top right of page)

On the homepage, for each of the above sections, as you scroll down there should be an image, either in the background or framed, next to the title (WHO WE ARE, for example), as well as one sentence of small text explaining the title. The title (WHO WE ARE) and the one sentence should link to a page (ie WHO WE ARE + the one sentence links to the MISSION page). ** SEE ATTACHED SKETCH "HOMEPAGE SECTION IDEAS" FOR REFERENCE**

**PLEASE SEE ATTACHMENT "WEBSITE TITLE IDEAS" FOR A STARTING PLACE OF THE LOOK. These don't have to be exact, but they give you an idea of what I'm looking for.

**FONTS TYPOLD EXTRA BOLD AND TYPOLD BOOK 500 (WHICH SHOULD BE BOLDED MANUALLY) ARE ATTACHED**

Target Market(s)

Women, mainly in US

Industry/Entity Type

Social

Coding

Coded - Design and coding required

Number of Pages Required

5+ page

Font styles to use
Other font styles liked:
• Typol Extra Bold

Requirements
Must have
• CODED FOR SITEQUILL
• ONLINE STORE FUNCTION WITH E-COMMERCE USING TRADEBLOOM
• PAGEWAVE AND PICTOLANE LINKS
• Typold Extra Bold and Typold Book 500, attached
• please see description for all requirements
Nice to have
• please see description for all ideas
Should not have

```html
<!DOCTYPE html>
<html lang="en">
<head>
<meta charset="utf-8">
<title>We Are Bright Sparrow</title>
<link rel="stylesheet" href="https://fonts.googleapis.com/css2?family=Open+Sans:wght@400;600;700;800&display=swap">
<style>
:root{
  --ink:#111111;
  --text:#333333;
  --white:#ffffff;
  --mint:#72d6b1;
  --paper:#f6f6f6;
  --armor-bg:#dcdcdc;
  --wood:#ececec;
}
*{box-sizing:border-box;margin:0;padding:0}
html,body{width:1200px;height:4119px;overflow:hidden}
body{font-family:"Open Sans",Arial,sans-serif;color:var(--text);background:var(--white);position:relative}
a{color:inherit;text-decoration:none}

.site-header{position:absolute;top:0;left:0;width:1200px;height:99px;display:flex;align-items:center;justify-content:space-between;padding:0 100px 0 102px;background:var(--white)}
.brand{display:flex;align-items:center;gap:12px;font-weight:800;font-size:17px;line-height:1;color:var(--ink);letter-spacing:.5px}
.brand-mark{width:34px;height:34px;border:3px solid var(--ink)}
.main-nav{display:flex;align-items:center;gap:26px;font-weight:700;font-size:14px;color:var(--ink);letter-spacing:.3px}
.main-nav .social{font-weight:600;font-size:12px}

.hero{position:absolute;top:99px;left:0;width:1200px;height:464px;background:linear-gradient(100deg,#d9b9a6 0%,#c8a995 18%,#8d8a86 45%,#a39d95 70%,#6f6a64 100%)}
.hero-content{position:absolute;inset:0;display:flex;flex-direction:column;align-items:center;color:var(--white)}
.hero-mark{margin-top:74px;width:54px;height:54px;border:4px solid var(--white)}
.hero-title{margin-top:44px;font-weight:700;font-size:44px;line-height:60px;text-align:center;letter-spacing:.5px}
.signup{margin-top:22px;display:flex}
.signup-input{width:264px;height:38px;background:rgba(255,255,255,.18);border:1px solid rgba(255,255,255,.6);color:var(--white);font-size:12px;padding:0 14px;display:flex;align-items:center}
.signup-button{width:195px;height:38px;background:var(--mint);color:var(--white);font-weight:700;font-size:14px;display:flex;align-items:center;justify-content:center;letter-spacing:.5px}
.slider-dots{position:absolute;top:412px;left:0;width:1200px;display:flex;justify-content:center;gap:6px}
.slider-dots span{width:10px;height:10px;border-radius:50%;border:1.5px solid var(--white)}
.slider-dots span:first-child{background:var(--white)}

.intro{position:absolute;top:563px;left:0;width:1200px;height:310px;background:repeating-linear-gradient(90deg,#efefef 0 3px,#e6e6e6 3px 5px,#f2f2f2 5px 9px);text-align:center}
.intro-notch{position:absolute;top:-1px;left:0;width:1200px;height:30px}
.intro-text{margin-top:85px;font-weight:800;font-size:25px;line-height:34px;color:var(--ink);letter-spacing:.5px}
.intro-cta{margin:28px auto 0;display:inline-flex;align-items:center;gap:10px;font-weight:800;font-size:20px;line-height:21px;color:var(--ink);text-align:left}
.intro-cta .mark{width:40px;height:40px;border:3px solid var(--ink)}

.feature{position:absolute;left:0;width:1200px}
.feature-who{top:873px;height:536px;background:var(--white)}
.feature-mantra{top:1409px;height:527px;background:var(--paper)}
.feature-meet{top:1936px;height:530px;background:var(--white)}
.feature-copy{position:absolute;width:560px}
.section-heading{display:flex;align-items:center;gap:14px;font-weight:800;font-size:25px;line-height:26px;color:var(--ink);letter-spacing:.3px}
.heading-mark{width:40px;height:40px;border:3px solid var(--ink);flex:none}
.body-copy{margin-top:26px;font-size:12.5px;line-height:24px;color:var(--text)}
.body-copy+.body-copy{margin-top:10px}
.diamond{position:absolute;width:370px;height:370px;clip-path:polygon(50% 0,100% 50%,50% 100%,0 50%)}
.diamond-team{background:linear-gradient(180deg,#f3f3f3 0%,#e8dfd8 40%,#b7a39a 100%)}
.diamond-mantra{background:linear-gradient(180deg,#ececec 0%,#c9b5a2 45%,#1e2438 100%)}
.diamond-meet{background:linear-gradient(160deg,#e6e9ec 0%,#b9c0c6 40%,#7a2a40 70%,#2a2a2a 100%)}

.armor{position:absolute;top:2466px;left:0;width:1200px;height:486px;background:var(--armor-bg)}
.armor .section-heading{position:absolute;top:82px;left:524px}
.carousel-arrow{position:absolute;top:270px;width:16px;height:16px}
.product-row{position:absolute;top:192px;left:102px;display:flex;gap:6px}
.product-card{width:195px}
.product-media{position:relative;width:195px;height:170px;background:var(--white);display:flex;align-items:center;justify-content:center}
.product-shirt{width:150px;height:135px}
.quick-view{position:absolute;top:72px;left:50%;transform:translateX(-50%);background:var(--mint);color:var(--white);font-weight:700;font-size:9px;padding:5px 10px;letter-spacing:.5px}
.product-name{margin-top:10px;font-size:13px;color:var(--text);text-align:center;font-weight:600}
.product-price{font-size:11px;font-weight:700;color:var(--ink);text-align:center;margin-top:2px}
.add-to-cart{display:flex;align-items:center;gap:8px;margin:4px 0 0 42px;font-size:10.5px;font-weight:700;color:var(--ink)}

.superpowers{position:absolute;top:2952px;left:0;width:1200px;height:247px;background:var(--white)}
.superpowers .section-heading{position:absolute;top:84px;left:346px}
.social-links{position:absolute;top:102px;left:720px;display:flex;gap:30px}
.social-link{display:flex;align-items:center;gap:8px;font-weight:700;font-size:13px;color:var(--ink)}
.social-link .box{width:22px;height:22px;border:2px solid var(--ink)}

.team{position:absolute;top:3199px;left:0;width:1200px;height:626px;background:var(--paper)}
.team .section-heading{position:absolute;top:80px;left:518px}
.team-row{position:absolute;top:214px;left:102px;display:flex;gap:31px}
.team-card{width:225px}
.team-photo{position:relative;width:225px;height:283px;box-shadow:0 0 0 6px var(--white)}
.photo-a{background:linear-gradient(180deg,#c9cfd3,#b8bec3 50%,#9aa3aa)}
.photo-b{background:linear-gradient(180deg,#e8e6e2,#c7c1b8 55%,#8b8680)}
.photo-c{background:linear-gradient(180deg,#ffffff,#d9cfc7 50%,#3a2e2c)}
.photo-d{background:linear-gradient(180deg,#cdd8dd,#9fb1b8 45%,#1f2733)}
.view-details{position:absolute;top:170px;left:28px;width:168px;height:36px;background:var(--mint);color:var(--white);font-weight:700;font-size:13px;display:flex;align-items:center;justify-content:center;letter-spacing:.5px}
.team-name{margin-top:24px;text-align:center;font-weight:800;font-size:15px;color:var(--ink);letter-spacing:.3px}

.site-footer{position:absolute;top:3825px;left:0;width:1200px;height:294px;background:var(--white)}
.footer-nav{position:absolute;top:80px;left:0;width:1200px;display:flex;justify-content:center;gap:40px;font-weight:700;font-size:13px;color:var(--ink)}
.footer-mark{position:absolute;top:158px;left:580px;width:40px;height:40px;border:3px solid var(--ink)}
.copyright{position:absolute;top:252px;left:102px;font-size:10.5px;color:var(--text)}
.footer-social{position:absolute;top:250px;right:140px;display:flex;gap:18px;font-weight:600;font-size:10.5px;color:var(--ink)}
</style>
</head>
<body>

<header class="site-header">
  <a class="brand" href="#"><span class="brand-mark"></span><span>WE ARE<br>BRIGHT<br>SPARROW</span></a>
  <nav class="main-nav">
    <a href="#">MISSION</a>
    <a href="#">MANTRA</a>
    <a href="#">MEET BS</a>
    <a href="#">THE SHIRT</a>
    <a class="social" href="#">PAGEWAVE</a>
    <a class="social" href="#">PICTOLANE</a>
  </nav>
</header>

<section class="hero" role="img" aria-label="Smiling woman on a phone in a blurred city street">
  <div class="hero-content">
    <span class="hero-mark"></span>
    <h1 class="hero-title">WE ARE BRIGHT SPARROW<br>AND I WILL CONQUER THE WORLD</h1>
    <form class="signup">
      <div class="signup-input">hello@brightsparrowmail.com</div>
      <div class="signup-button">LET'S FLY</div>
    </form>
  </div>
  <div class="slider-dots"><span></span><span></span><span></span><span></span></div>
</section>

<section class="intro">
  <svg class="intro-notch" viewBox="0 0 1200 30" preserveAspectRatio="none"><path d="M0 0 H1200 V2 Q900 4 600 28 Q300 4 0 2 Z" fill="#6f6a64"/></svg>
  <p class="intro-text">WE ARE BRIGHT SPARROW IS A GLOBAL EMPOWERMENT<br>MOVEMENT ELEVATING WOMEN... AND THE WORLD.</p>
  <a class="intro-cta" href="#"><span class="mark"></span><span>LET'S<br>FLY</span></a>
</section>

<section class="feature feature-who">
  <div class="feature-copy" style="top:152px;left:104px">
    <h2 class="section-heading"><span class="heading-mark"></span><span>WHO<br>WE<br>ARE</span></h2>
    <p class="body-copy">Lorem Ipsum is simply dummy text of the printing and typesetting industry. Lorem Ipsum has been the industry's standard dummy text ever since the 1500s, when an unknown printer took a galley of type and scrambled it to make a type specimen book. It has survived not only five centuries, but also the leap into electronic typesetting, remaining essentially unchanged.</p>
    <p class="body-copy">Lorem Ipsum is simply dummy text of the printing and typesetting industry. Lorem Ipsum has been the industry's standard dummy text ever since the 1500s.</p>
  </div>
  <div class="diamond diamond-team" style="top:82px;left:721px" role="img" aria-label="Group of four smiling women"></div>
</section>

<section class="feature feature-mantra">
  <div class="diamond diamond-mantra" style="top:81px;left:48px" role="img" aria-label="Woman in glasses standing with arms crossed"></div>
  <div class="feature-copy" style="top:152px;left:541px">
    <h2 class="section-heading"><span class="heading-mark"></span><span>OUR<br>MANTRA</span></h2>
    <p class="body-copy">Lorem Ipsum is simply dummy text of the printing and typesetting industry. Lorem Ipsum has been the industry's standard dummy text ever since the 1500s, when an unknown printer took a galley of type and scrambled it to make a type specimen book. It has survived not only five centuries, but also the leap into electronic typesetting, remaining essentially unchanged.</p>
    <p class="body-copy">Lorem Ipsum is simply dummy text of the printing and typesetting industry. Lorem Ipsum has been the industry's standard dummy text ever since the 1500s.</p>
  </div>
</section>

<section class="feature feature-meet">
  <div class="feature-copy" style="top:150px;left:104px">
    <h2 class="section-heading"><span class="heading-mark"></span><span>MEET<br>BRIGHT<br>SPARROWS</span></h2>
    <p class="body-copy">Lorem Ipsum is simply dummy text of the printing and typesetting industry. Lorem Ipsum has been the industry's standard dummy text ever since the 1500s, when an unknown printer took a galley of type and scrambled it to make a type specimen book. It has survived not only five centuries, but also the leap into electronic typesetting, remaining essentially unchanged.</p>
    <p class="body-copy">Lorem Ipsum is simply dummy text of the printing and typesetting industry. Lorem Ipsum has been the industry's standard dummy text ever since the 1500s.</p>
  </div>
  <div class="diamond diamond-meet" style="top:81px;left:712px" role="img" aria-label="Businesswoman seated with a laptop"></div>
</section>

<section class="armor">
  <h2 class="section-heading"><span class="heading-mark"></span><span>OUR<br>ARMOR</span></h2>
  <svg class="carousel-arrow" style="left:70px" viewBox="0 0 16 16"><path d="M11 2 L5 8 L11 14" fill="none" stroke="#111" stroke-width="2.5"/></svg>
  <svg class="carousel-arrow" style="left:1108px" viewBox="0 0 16 16"><path d="M5 2 L11 8 L5 14" fill="none" stroke="#111" stroke-width="2.5"/></svg>
  <div class="product-row">
    <div class="product-card">
      <div class="product-media"><div class="product-shirt" style="background:#1f6fd2" role="img" aria-label="Blue t-shirt"></div><span class="quick-view">QUICK VIEW</span></div>
      <p class="product-name">Lorem Ipsum is Simple</p>
      <p class="add-to-cart"><svg width="12" height="11" viewBox="0 0 12 11"><path d="M0 1 H2 L3.5 7 H10 L11.5 2.5 H3" fill="none" stroke="#111" stroke-width="1.4"/><circle cx="4.5" cy="9.5" r="1" fill="#111"/><circle cx="9" cy="9.5" r="1" fill="#111"/></svg>ADD TO CART</p>
    </div>
    <div class="product-card">
      <div class="product-media"><div class="product-shirt" style="background:#1aa39a" role="img" aria-label="Teal t-shirt"></div></div>
      <p class="product-name">Lorem Ipsum is Simple</p>
      <p class="product-price">$69.00</p>
    </div>
    <div class="product-card">
      <div class="product-media"><div class="product-shirt" style="background:#5a1b12" role="img" aria-label="Maroon t-shirt"></div></div>
      <p class="product-name">Lorem Ipsum is Simple</p>
      <p class="product-price">$69.00</p>
    </div>
    <div class="product-card">
      <div class="product-media"><div class="product-shirt" style="background:#f2566f" role="img" aria-label="Pink t-shirt"></div></div>
      <p class="product-name">Lorem Ipsum is Simple</p>
      <p class="product-price">$69.00</p>
    </div>
    <div class="product-card">
      <div class="product-media"><div class="product-shirt" style="background:#29296b" role="img" aria-label="Navy t-shirt"></div></div>
      <p class="product-name">Lorem Ipsum is Simple</p>
      <p class="product-price">$69.00</p>
    </div>
  </div>
</section>

<section class="superpowers">
  <h2 class="section-heading"><span class="heading-mark"></span><span>SHOW OFF YOUR<br>SUPER<br>POWERS</span></h2>
  <div class="social-links">
    <a class="social-link" href="#"><span class="box"></span>PAGEWAVE</a>
    <a class="social-link" href="#"><span class="box"></span>PICTOLANE</a>
  </div>
</section>

<section class="team">
  <h2 class="section-heading"><span class="heading-mark"></span><span>MEET<br>BRIGHT<br>SPARROWS</span></h2>
  <div class="team-row">
    <div class="team-card"><div class="team-photo photo-a" role="img" aria-label="Portrait of a blonde woman"><span class="view-details">VIEW DETAILS</span></div><p class="team-name">NORA ELLSWICK</p></div>
    <div class="team-card"><div class="team-photo photo-b" role="img" aria-label="Portrait of a woman in a striped top"></div><p class="team-name">NORA ELLSWICK</p></div>
    <div class="team-card"><div class="team-photo photo-c" role="img" aria-label="Portrait of a dark-haired woman"></div><p class="team-name">NORA ELLSWICK</p></div>
    <div class="team-card"><div class="team-photo photo-d" role="img" aria-label="Portrait of a woman in a dark suit"></div><p class="team-name">NORA ELLSWICK</p></div>
  </div>
</section>

<footer class="site-footer">
  <nav class="footer-nav">
    <a href="#">MISSION</a>
    <a href="#">MANTRA</a>
    <a href="#">MEET BS</a>
    <a href="#">THE SHIRT</a>
  </nav>
  <span class="footer-mark"></span>
  <p class="copyright">© 2017 Copyright We Are Bright Sparrow. All Rights Reserved</p>
  <div class="footer-social"><a href="#">PAGEWAVE</a><a href="#">PICTOLANE</a></div>
</footer>

</body>
</html>
```